Rebrand stationary with recently completed logo design

Need new business cards, thank you cards, letterhead, envelopes and presentation folders. The designs will be sent to a separate production firm so I need the files to be print ready.

My contact info
Reko Haliburn

Office 604-318-5047
Fax 604-371-8054

Email reko@glazemark.ca
website www.glazemark.ca

315-14720 62nd Avenue,
Langley, BC, V2K 3R8

Target Market(s)

Homeowners, businesses and contractors

Industry/Entity Type

Business

Font styles to use
Sans Serif

Colors
34a7d7

Requirements
Must have
• Like to have one side of the business card a solid color with the logo in all white. The side with all the text to be a white background
• I find the current blue on the front of the card with the white logo too dark.
Should not have
• Gradient colors

```html
<!DOCTYPE html>
<html lang="en">
<head>
<meta charset="utf-8">
<title>Glazemark Presentation Folder</title>
<link href="https://fonts.googleapis.com/css2?family=Roboto:wght@300;400&family=Lato:ital,wght@0,400;1,400&display=swap" rel="stylesheet">
<style>
  :root {
    --page-bg: #e6e7e9;
    --brand-blue: #0599dc;
    --paper: #ffffff;
    --sky-light: #bfe0f6;
    --sky-mid: #5fa8dc;
    --glass-deep: #1f6ea8;
    --logo-grey: #5a5a5c;
    --trim: #9aa3ab;
  }
  * { margin: 0; padding: 0; box-sizing: border-box; }
  html, body { width: 1200px; height: 882px; overflow: hidden; background: var(--page-bg); }
  .folder {
    position: absolute; left: 57px; top: 54px; width: 1091px; height: 770px;
    display: flex; border: 1px solid var(--trim);
  }
  .panel { position: relative; width: 50%; height: 100%; overflow: hidden; }

  /* back cover */
  .back-cover { background: var(--brand-blue); border-right: 1px solid var(--trim); }
  .back-cover .sweep { position: absolute; left: 0; top: 0; width: 100%; height: 100%; }
  .back-brand {
    position: absolute; left: 52px; top: 636px;
    display: flex; align-items: center; gap: 8px;
    font-family: "Roboto", sans-serif; font-weight: 400; font-size: 21px;
    letter-spacing: 1px; color: var(--paper);
  }
  .back-brand .mark { width: 12px; height: 12px; background: var(--paper); }
  .contact {
    position: absolute; left: 53px; top: 690px;
    display: grid; grid-template-columns: auto auto auto; column-gap: 9px; row-gap: 2px;
    font-family: "Lato", sans-serif; font-style: italic; font-size: 10.5px; color: var(--paper);
  }
  .contact .item { display: flex; align-items: flex-start; gap: 4px; white-space: nowrap; line-height: 13px; }
  .contact svg { width: 9px; height: 9px; margin-top: 2px; flex: none; }
  .contact .address { grid-row: span 2; }

  /* front cover */
  .front-cover { background: var(--paper); }
  .cover-photo {
    position: absolute; inset: 0;
    background:
      radial-gradient(circle at 48% 28%, rgba(255,255,255,0.85) 0, rgba(255,255,255,0) 22%),
      linear-gradient(165deg, var(--sky-light) 0%, var(--sky-mid) 40%, var(--glass-deep) 100%);
  }
  .front-brand {
    position: absolute; right: 60px; top: 106px;
    display: flex; align-items: center; gap: 8px;
    font-family: "Roboto", sans-serif; font-weight: 400; font-size: 24px;
    letter-spacing: 1px; color: var(--logo-grey);
  }
  .front-brand .mark { width: 13px; height: 13px; background: var(--logo-grey); }
  .cover-title {
    position: absolute; left: 52px; top: 412px;
    font-family: "Roboto", sans-serif; font-weight: 300; color: var(--paper);
  }
  .cover-title h1 { font-weight: 300; font-size: 39px; line-height: 46px; }
  .cover-title p { font-size: 20px; margin-top: 2px; }
  .film-types {
    position: absolute; left: 309px; top: 650px; width: 197px; height: 68px;
    border: 1px dashed rgba(255,255,255,0.85); background: rgba(255,255,255,0.18);
    display: flex; align-items: center; justify-content: center; gap: 3px;
    font-family: "Roboto", sans-serif; font-weight: 300; color: var(--paper);
  }
  .film-types ul { list-style: none; text-align: right; font-size: 13px; line-height: 12px; }
  .film-types strong { font-weight: 300; font-size: 50px; line-height: 44px; }
</style>
</head>
<body>
  <main class="folder">
    <section class="panel back-cover">
      <svg class="sweep" viewBox="0 0 545 770" preserveAspectRatio="none" aria-hidden="true">
        <path d="M545 585 C520 590 500 578 480 590 C455 610 470 660 420 700 C380 735 320 755 270 770 L545 770 Z" fill="#ffffff"/>
      </svg>
      <div class="back-brand"><span class="mark"></span>GLAZEMARK</div>
      <address class="contact">
        <span class="item"><svg viewBox="0 0 10 10"><path d="M2 1l2 2-1 1.3c.6 1.2 1.5 2.1 2.7 2.7L7 6l2 2-1.3 1.3C4.5 9 1 5.5.7 2.3z" fill="none" stroke="#fff" stroke-width=".8"/></svg>604-318-5047</span>
        <span class="item"><svg viewBox="0 0 10 10"><rect x=".5" y="2" width="9" height="6" fill="none" stroke="#fff" stroke-width=".8"/><path d="M.5 2l4.5 3.5L9.5 2" fill="none" stroke="#fff" stroke-width=".8"/></svg>reko@glazemark.ca</span>
        <span class="item address"><svg viewBox="0 0 10 10"><path d="M5 9.5C3 7 2 5.5 2 4a3 3 0 016 0c0 1.5-1 3-3 5.5z" fill="none" stroke="#fff" stroke-width=".8"/><circle cx="5" cy="4" r="1" fill="#fff"/></svg><span>315-14720 62nd Avenue,<br>Langley, BC, V2K 3R8</span></span>
        <span class="item"><svg viewBox="0 0 10 10"><rect x="1.5" y="3.5" width="7" height="5" fill="none" stroke="#fff" stroke-width=".8"/><rect x="3" y="1" width="4" height="2.5" fill="none" stroke="#fff" stroke-width=".8"/></svg>604-371-8054</span>
        <span class="item"><svg viewBox="0 0 10 10"><circle cx="5" cy="5" r="4.2" fill="none" stroke="#fff" stroke-width=".8"/><path d="M1 5h8M5 .8c-2 2.5-2 5.9 0 8.4M5 .8c2 2.5 2 5.9 0 8.4" fill="none" stroke="#fff" stroke-width=".7"/></svg>www.glazemark.ca</span>
      </address>
    </section>

    <section class="panel front-cover">
      <div class="cover-photo" role="img" aria-label="Photograph looking up at glass office towers against a bright blue sky with sun flare"></div>
      <div class="front-brand"><span class="mark"></span>GLAZEMARK</div>
      <div class="cover-title">
        <h1>Protective Security<br>Window Film</h1>
        <p>A Strong, Safe and Simple Solution</p>
      </div>
      <div class="film-types">
        <ul><li>SOLAR</li><li>FROSTED</li><li>SECURITY</li></ul>
        <strong>FILM</strong>
      </div>
    </section>
  </main>
</body>
</html>
```